Varlo Shawarma Restaurant packging desgin

I want a packging desgin for my new Shawarma restaurant. The desgin should be modern and simple. I have added the logo and the identity in the attachment in PSD format so you can use it in the desgin. I also added some packging idea you may use it as background of your desgin. The main colors to be used is Red, grey, black and white.
Updates

Project Deadline Extended
Reason: Still i did not find an attractive desgin. I will try to provied you with feedback for each post

Target Market(s)

Food industry

Industry/Entity Type

Fast Food Restaurant

Font styles to use
Sans Serif

Colors
ec1f27
000000
919191
ffffff
eeeeee

Requirements
Must have
• The logo and the name VARLO. All boxes should be in the same theme
Nice to have
• Creative desgin and Twitter and instagram logo on the side
Should not have
• real food pictures

```html
<!DOCTYPE html>
<html lang="en">
<head>
<meta charset="utf-8">
<title>Varlo Shawarma Restaurant – Cup Packaging</title>
<link rel="stylesheet" href="https://fonts.googleapis.com/css2?family=Fira+Sans+Condensed:wght@600;800&display=swap">
<style>
  :root {
    --brand-red: #ec1f27;
    --deep-red: #b3141b;
    --rim-red: #d0161e;
    --grey: #919191;
    --light-grey: #a7a9ac;
    --white: #ffffff;
    --paper: #ffffff;
  }
  html, body {
    margin: 0;
    padding: 0;
    width: 1200px;
    height: 1200px;
    overflow: hidden;
    background: var(--paper);
  }
  .sheet {
    display: block;
    width: 1200px;
    height: 1200px;
  }
  .wordmark {
    font-family: "Fira Sans Condensed", sans-serif;
    font-weight: 800;
    fill: var(--white);
    letter-spacing: 2px;
  }
  .flavour-name {
    font-family: "Fira Sans Condensed", sans-serif;
    font-weight: 600;
    fill: var(--white);
    font-size: 26px;
  }
  .red-fill { fill: var(--brand-red); }
  .rim { fill: var(--rim-red); }
  .pattern-area { fill: url(#grey-fade); }
  .mark-dot { fill: var(--white); }
  .badge-ring { fill: none; stroke: var(--white); stroke-width: 5; }
  .badge-art { fill: var(--deep-red); }
</style>
</head>
<body>
<svg class="sheet" viewBox="0 0 1200 1200" xmlns="http://www.w3.org/2000/svg">
  <defs>
    <linearGradient id="grey-fade" x1="0" y1="0" x2="1" y2="0">
      <stop offset="0" stop-color="#a7a9ac" stop-opacity="0.95"/>
      <stop offset="1" stop-color="#a7a9ac" stop-opacity="0"/>
    </linearGradient>
    <clipPath id="lid-face-left"><circle cx="300" cy="280" r="196"/></clipPath>
    <clipPath id="lid-face-right"><circle cx="900" cy="280" r="196"/></clipPath>
    <clipPath id="wrap-left"><polygon points="70,560 530,560 490,1080 110,1080"/></clipPath>
    <clipPath id="wrap-right"><polygon points="670,560 1130,560 1090,1080 710,1080"/></clipPath>
  </defs>

  <!-- Lid: chicken -->
  <g class="lid lid-chicken">
    <circle class="rim" cx="300" cy="280" r="214"/>
    <circle class="red-fill" cx="300" cy="280" r="196"/>
    <rect class="pattern-area" x="100" y="90" width="160" height="250" clip-path="url(#lid-face-left)" role="img" aria-label="Grey angled stripe decoration"/>
    <circle class="mark-dot" cx="300" cy="200" r="34"/>
    <text class="wordmark" x="300" y="300" font-size="64" text-anchor="middle">VARLO</text>
  </g>

  <!-- Lid: beef -->
  <g class="lid lid-beef">
    <circle class="rim" cx="900" cy="280" r="214"/>
    <circle class="red-fill" cx="900" cy="280" r="196"/>
    <rect class="pattern-area" x="700" y="90" width="160" height="250" clip-path="url(#lid-face-right)" role="img" aria-label="Grey angled stripe decoration"/>
    <circle class="mark-dot" cx="900" cy="200" r="34"/>
    <text class="wordmark" x="900" y="300" font-size="64" text-anchor="middle">VARLO</text>
  </g>

  <!-- Cup wrap: chicken -->
  <g class="wrap wrap-chicken" clip-path="url(#wrap-left)">
    <polygon class="red-fill" points="70,560 530,560 490,1080 110,1080"/>
    <rect class="pattern-area" x="70" y="560" width="130" height="420" role="img" aria-label="Grey angled stripe decoration"/>
    <circle class="mark-dot" cx="300" cy="720" r="42"/>
    <text class="wordmark" x="300" y="840" font-size="64" text-anchor="middle">VARLO</text>
    <g class="flavour-badge">
      <circle class="badge-ring" cx="300" cy="1040" r="118"/>
      <text class="flavour-name" x="300" y="972" text-anchor="middle">Chicken</text>
      <rect class="badge-art" x="240" y="990" width="120" height="88" rx="10" role="img" aria-label="Line drawing of a chicken drumstick"/>
    </g>
  </g>

  <!-- Cup wrap: beef -->
  <g class="wrap wrap-beef" clip-path="url(#wrap-right)">
    <polygon class="red-fill" points="670,560 1130,560 1090,1080 710,1080"/>
    <rect class="pattern-area" x="670" y="560" width="130" height="420" role="img" aria-label="Grey angled stripe decoration"/>
    <circle class="mark-dot" cx="900" cy="720" r="42"/>
    <text class="wordmark" x="900" y="840" font-size="64" text-anchor="middle">VARLO</text>
    <g class="flavour-badge">
      <circle class="badge-ring" cx="900" cy="1040" r="118"/>
      <text class="flavour-name" x="900" y="972" text-anchor="middle">Beef</text>
      <rect class="badge-art" x="840" y="990" width="120" height="88" rx="10" role="img" aria-label="Line drawing of a beef cut on a bone"/>
    </g>
  </g>
</svg>
</body>
</html>
```